Box for a Bold Bathroom - stylish minimalist package for a modern upscale brand

We need an adaptable package design using a color label on a brown box, or just a brown box with 2 or 3 color printing. The best design would be one that is adaptable for either use.

Our first products launching under this brand will be a series of medicine cabinets and mirrors, and our cartons can vary in size from 500x100x600 mm to 1200x300x1000 mm

About us: we produce a variety of bathroom fixtures including medicine cabinets, mirrors, vanities, etc. You've likely seen our products - we do manufacturing for Brantley, Marlowe, Thistle Cove, Dunmore & Pike, and others.

A version of our logo is attached for reference; we use it in a variety of color mixes depending on application. Vector available if needed or can be used FPO and our team will replace.

These are our colors, please take note and ignore the 'color' field:

Light Blue: C:66%/M:6%/Y:22%/K:0%; H:189° S:65% B:78%
Light Grey: C:35%/M:26%/Y:24%/K:0%; H:213° S:5% B:70%
Dark Blue: C:90%/M:50%/Y:44%/K:20%; H:189° S:82% B:43%
Dark Grey: C:70%/M:60%/Y:54%/K:38%; H:213° S:11% B:30%

Reason: Some revisions still outstanding before we can make selection, and some submissions we have agreed to wait for. Please submit all work ASAP so our team can provide feedback to you. Thanks!

Target Market(s)

DIY'ers; home renovators

Industry/Entity Type

Home Improvement

Font styles to use
Sans Serif

Requirements
Must have
• 1. Brand logo w/ logotype
• 2. Brand name without logo (can be on shipping mark side)
• 3. Multi-lingual En/Fr/Es (you do not need to include multi-lingual content but must allow space for our own translations if you do not)
• 4. Shipping/Handling Glyphs on 5 sides (all but bottom)
• i.e. fragile, this way up, team lift or mech lift, clamp or no clamp, max-stack
• 5. Two sides should include a marked 4" x 4" area for affixing labels (e.g. UPC, SSCC, etc.) ideally with a dotted line or corner marks or similar.
• 6. Shipping mark details or space for them (should be on the smallest side, only needed on one but can be on both) [see example file of shipping mark informations]
Nice to have
• Design that can be used either with color label on brown box, or brown box only.
• If designing for color label; please see the sample images included. Lifestyle should be prominent, the inside photo being smaller to help show interior features. These photos are obviously not useful for brown-box design.

```html
<!DOCTYPE html>
<html lang="en">
<head>
<meta charset="utf-8">
<title>Clearhaven carton — flat layout</title>
<link rel="stylesheet" href="https://fonts.googleapis.com/css2?family=Jost:wght@400&display=swap">
<style>
  :root {
    --backdrop: #ececec;
    --kraft: #c99a65;
    --kraft-top: #d4a874;
    --kraft-side: #cfa26d;
    --ink: #35302b;
    --light-blue: #46b8c7;
  }
  html, body {
    margin: 0;
    padding: 0;
    width: 1200px;
    height: 1037px;
    overflow: hidden;
    background: var(--backdrop);
  }
  .carton {
    display: block;
    width: 1200px;
    height: 1037px;
    font-family: "Jost", "Helvetica Neue", Arial, sans-serif;
  }
  .panel-front { fill: var(--kraft); }
  .panel-top { fill: var(--kraft-top); }
  .panel-side { fill: var(--kraft-side); }
  .guide-line { fill: none; stroke: var(--ink); stroke-width: 7; stroke-linecap: butt; stroke-linejoin: miter; }
  .label-area { fill: none; stroke: var(--ink); stroke-width: 3; stroke-dasharray: 6 12; }
  .brand-name { fill: var(--ink); font-weight: 400; }
  .brand-dot { fill: var(--light-blue); }
  .glyph-box { fill: none; stroke: var(--ink); stroke-width: 2.5; }
  .glyph-mark { fill: none; stroke: var(--ink); stroke-width: 2.5; stroke-linecap: round; stroke-linejoin: round; }
  .glyph-fill { fill: var(--ink); }
</style>
</head>
<body>
<svg class="carton" viewBox="0 0 1200 1037" xmlns="http://www.w3.org/2000/svg">
  <defs>
    <g id="glyph-team-lift">
      <rect class="glyph-box" x="0" y="0" width="38" height="38"/>
      <circle class="glyph-fill" cx="10" cy="10" r="3"/>
      <circle class="glyph-fill" cx="28" cy="10" r="3"/>
      <path class="glyph-mark" d="M10 15 V32 M28 15 V32 M10 20 H28"/>
    </g>
    <g id="glyph-recycle">
      <rect class="glyph-box" x="0" y="0" width="38" height="38"/>
      <path class="glyph-mark" d="M19 9 L28 25 H10 Z"/>
    </g>
    <g id="glyph-care">
      <rect class="glyph-box" x="0" y="0" width="38" height="38"/>
      <path class="glyph-mark" d="M8 16 L13 30 H25 L30 16 M19 12 V22"/>
    </g>
    <g id="glyph-up">
      <rect class="glyph-box" x="0" y="0" width="38" height="38"/>
      <path class="glyph-mark" d="M13 30 V9 M9 14 L13 9 L17 14 M25 30 V9 M21 14 L25 9 L29 14 M8 32 H30"/>
    </g>
    <g id="glyph-fragile">
      <rect class="glyph-box" x="0" y="0" width="38" height="38"/>
      <path class="glyph-mark" d="M11 8 H27 L25 18 Q19 24 13 18 Z M19 22 V30 M13 30 H25"/>
    </g>
    <g id="glyph-dry">
      <rect class="glyph-box" x="0" y="0" width="38" height="38"/>
      <path class="glyph-mark" d="M7 19 Q19 5 31 19 Z M19 19 V29 Q19 32 16 31"/>
    </g>
    <g id="glyph-row">
      <use href="#glyph-team-lift"/>
      <use href="#glyph-recycle" x="45"/>
      <use href="#glyph-care" x="90"/>
      <use href="#glyph-up" x="135"/>
      <use href="#glyph-fragile" x="180"/>
      <use href="#glyph-dry" x="225"/>
    </g>
  </defs>

  <!-- top panel -->
  <g class="top-face" transform="translate(170 110)">
    <rect class="panel-top" x="0" y="0" width="720" height="130"/>
    <circle class="brand-dot" cx="318" cy="55" r="10"/>
    <text class="brand-name" x="336" y="63" font-size="22" letter-spacing="3">CLEARHAVEN</text>
    <g transform="translate(560 90) scale(0.55)">
      <use href="#glyph-row"/>
    </g>
  </g>

  <!-- front panel -->
  <g class="front-face" transform="translate(170 250)">
    <rect class="panel-front" x="0" y="0" width="720" height="600"/>

    <circle class="brand-dot" cx="64" cy="92" r="12"/>
    <text class="brand-name" x="84" y="100" font-size="22" letter-spacing="3">CLEARHAVEN</text>

    <path class="guide-line" d="M272 90 V200 H595 V262 H553"/>
    <path class="guide-line" d="M55 540 V230 H252"/>
    <text class="brand-name" x="268" y="243" font-size="32" letter-spacing="8">CLEARHAVEN</text>

    <rect class="label-area" x="95" y="420" width="120" height="120"/>

    <g transform="translate(452 500)">
      <use href="#glyph-row"/>
    </g>
  </g>

  <!-- side panel -->
  <g class="side-face" transform="translate(900 250)">
    <rect class="panel-side" x="0" y="0" width="130" height="600"/>

    <circle class="brand-dot" cx="65" cy="82" r="10"/>
    <text class="brand-name" x="65" y="120" font-size="13" letter-spacing="2" text-anchor="middle">CLEARHAVEN</text>

    <rect class="label-area" x="15" y="250" width="100" height="100"/>

    <g class="side-glyphs" transform="translate(11 480) scale(0.85)">
      <use href="#glyph-team-lift"/>
      <use href="#glyph-recycle" x="45"/>
      <use href="#glyph-care" x="90"/>
      <use href="#glyph-up" y="48"/>
      <use href="#glyph-fragile" x="45" y="48"/>
      <use href="#glyph-dry" x="90" y="48"/>
    </g>
  </g>
</svg>
</body>
</html>
```